Business card design for my company.
I would like the card's background colour to be black. You can also see our web site to get an idea of our brand. https://www.tmwhomecrafting.com.au/
- Name
- Email

```html
<!DOCTYPE html>
<html lang="en">
<head>
<meta charset="utf-8">
<title>TMW Home Crafting – Business Card</title>
<link rel="stylesheet" href="https://fonts.googleapis.com/css2?family=Poppins:wght@400;500;600;700&display=swap">
<style>
  :root {
    --ink: #000000;
    --paper: #ffffff;
    --brand-green: #14a04a;
    --backdrop: #d6d6d6;
    --card-shadow: rgba(0,0,0,0.28);
  }
  * { box-sizing: border-box; margin: 0; padding: 0; }
  html, body { width: 1200px; height: 961px; overflow: hidden; }
  body {
    background: var(--backdrop);
    font-family: "Poppins", sans-serif;
    position: relative;
  }
  .card {
    position: absolute;
    width: 600px;
    height: 367px;
    background: var(--ink);
    overflow: hidden;
    box-shadow: 0 14px 30px var(--card-shadow);
  }
  .card--front { left: 560px; top: 100px; }
  .card--back { left: 40px; top: 494px; }

  /* Front */
  .wordmark {
    position: absolute;
    color: var(--paper);
    font-weight: 600;
    letter-spacing: 0.06em;
    text-transform: uppercase;
    white-space: nowrap;
  }
  .card--front .wordmark { left: 36px; top: 34px; font-size: 24px; }
  .name-banner {
    position: absolute;
    right: 0; top: 100px;
    width: 270px; height: 62px;
    background: var(--brand-green);
    clip-path: polygon(0 50%, 34px 0, 100% 0, 100% 100%, 34px 100%);
    color: var(--paper);
    padding: 9px 18px 0 50px;
  }
  .name-banner__name { font-size: 20px; font-weight: 700; letter-spacing: 0.04em; line-height: 1.2; }
  .name-banner__title { font-size: 11px; font-weight: 500; letter-spacing: 0.12em; }
  .photo-strip {
    position: absolute;
    left: 0; right: 0; top: 180px; height: 120px;
    background: var(--brand-green);
    display: flex; gap: 5px;
    padding: 5px 5px 5px 0;
  }
  .photo { flex: 1; }
  .photo--living { background: linear-gradient(135deg, #8a5a34, #b9c8d0); }
  .photo--bathroom { background: linear-gradient(135deg, #f1f1ef, #9a9a98); }
  .photo--kitchen { background: linear-gradient(135deg, #c98a4e, #efe2cf); }
  .photo--facade { background: linear-gradient(135deg, #7a4524, #4c4f55); }
  .contact-bar {
    position: absolute;
    left: 0; right: 0; bottom: 0; height: 67px;
    background: var(--paper);
    display: flex; align-items: center; justify-content: center; gap: 22px;
    font-size: 15px; color: var(--ink);
  }
  .contact-item { display: flex; align-items: center; gap: 8px; }
  .contact-divider { width: 1px; height: 18px; background: var(--ink); }

  /* Back */
  .services { position: absolute; left: 40px; top: 34px; color: var(--paper); }
  .services__heading {
    color: var(--brand-green); font-size: 19px; font-weight: 700;
    letter-spacing: 0.03em; text-transform: uppercase; margin-bottom: 8px;
  }
  .services__list { list-style: none; font-size: 14px; line-height: 21px; }
  .services__list li::before { content: "✳"; color: var(--brand-green); margin-right: 10px; font-size: 12px; }
  .social { position: absolute; right: 40px; top: 218px; display: flex; gap: 6px; }
  .social__square { width: 24px; height: 24px; background: var(--brand-green); }
  .card--back .wordmark { right: 40px; bottom: 44px; font-size: 26px; }
</style>
</head>
<body>
  <section class="card card--front">
    <div class="wordmark">TMW Home Crafting</div>
    <div class="name-banner">
      <div class="name-banner__name">LIAM HARCOURT</div>
      <div class="name-banner__title">GENERAL MANAGER</div>
    </div>
    <div class="photo-strip">
      <div class="photo photo--living" role="img" aria-label="Photo of a timber-lined living room with a view"></div>
      <div class="photo photo--bathroom" role="img" aria-label="Photo of a bright bathroom with glass shower"></div>
      <div class="photo photo--kitchen" role="img" aria-label="Photo of a warm timber kitchen with pendant lights"></div>
      <div class="photo photo--facade" role="img" aria-label="Photo of a home facade with timber battens"></div>
    </div>
    <div class="contact-bar">
      <div class="contact-item">
        <svg width="18" height="18" viewBox="0 0 18 18" aria-hidden="true"><circle cx="9" cy="9" r="9" fill="#14a04a"/><path d="M6 5l2 2-1 1.2c.6 1.3 1.5 2.2 2.8 2.8L11 10l2 2-1.2 1.2C8.5 13 5 9.5 4.8 6.2z" fill="#fff"/></svg>
        <span>0412 555 318</span>
      </div>
      <div class="contact-divider"></div>
      <div class="contact-item">
        <svg width="18" height="18" viewBox="0 0 18 18" aria-hidden="true"><circle cx="9" cy="9" r="9" fill="#14a04a"/><rect x="4.5" y="6" width="9" height="6.5" fill="#fff"/><path d="M4.5 6l4.5 3.5L13.5 6" fill="none" stroke="#14a04a" stroke-width="1"/></svg>
        <span>info@tmwhomecrafting.com.au</span>
      </div>
    </div>
  </section>

  <section class="card card--back">
    <div class="services">
      <h2 class="services__heading">Our Services</h2>
      <ul class="services__list">
        <li>Custom homes</li>
        <li>Architectural homes</li>
        <li>New builds</li>
        <li>Renovations</li>
        <li>Extensions</li>
        <li>Alterations</li>
        <li>Project management</li>
        <li>Kitchens</li>
        <li>Bathrooms</li>
        <li>Shop fit outs</li>
        <li>Decks and more</li>
      </ul>
    </div>
    <div class="social" aria-label="Social media">
      <div class="social__square"></div>
      <div class="social__square"></div>
    </div>
    <div class="wordmark">TMW Home Crafting</div>
  </section>
</body>
</html>
```